BWP Business Card

A double sided business card based on your "Brindlewood Partners Ltd" Logo. To use the "BWP" logo on 1 side and the full company logo on the reverse.

Detials to be included:

Name: Tomas Wheeler
Postion: Consultant Orthotist & Expert Witness
T: +44 (0) 7700 938271
F: +44 (0) 7654 8820

```html
<!DOCTYPE html>
<html lang="en">
<head>
<meta charset="utf-8">
<title>BWP Business Card</title>
<link href="https://fonts.googleapis.com/css2?family=Crimson+Pro:wght@400;600;700&display=swap" rel="stylesheet">
<style>
  :root {
    --navy: #083a70;
    --grey: #9a9a9a;
    --grey-light: #b3b3b3;
    --paper: #ffffff;
    --backdrop: #e6e7ec;
    --text-grey: #8a8a8a;
  }
  html, body {
    margin: 0;
    width: 1200px;
    height: 987px;
    overflow: hidden;
    background: var(--backdrop);
    font-family: "Crimson Pro", Georgia, serif;
  }
  .sheet {
    position: relative;
    width: 1200px;
    height: 987px;
  }
  .card {
    position: absolute;
    left: 280px;
    width: 640px;
    height: 414px;
    background: var(--paper);
    border-radius: 28px;
    overflow: hidden;
    box-shadow: 0 6px 18px rgba(0,0,0,0.12);
  }
  .card--front { top: 38px; }
  .card--back { top: 535px; }

  .card__wave {
    position: absolute;
    inset: 0;
    width: 100%;
    height: 100%;
  }

  .brand {
    position: absolute;
    left: 40px;
    top: 40px;
    display: flex;
    align-items: center;
  }
  .brand__mark {
    display: flex;
    align-items: center;
    gap: 10px;
    padding-right: 22px;
    border-right: 1.5px solid var(--grey);
    height: 96px;
  }
  .brand__square {
    width: 22px;
    height: 22px;
    background: var(--navy);
  }
  .brand__initials {
    font-size: 52px;
    font-weight: 600;
    color: var(--navy);
    letter-spacing: 4px;
    line-height: 1;
  }
  .brand__words {
    padding-left: 22px;
  }
  .brand__name {
    font-size: 34px;
    font-weight: 600;
    color: var(--navy);
    text-transform: uppercase;
    line-height: 0.95;
    letter-spacing: 0.5px;
    margin: 0;
  }
  .brand__tagline {
    margin-top: 6px;
    padding-top: 3px;
    border-top: 1.5px solid #444;
    font-size: 11px;
    font-weight: 600;
    color: #333;
    text-transform: uppercase;
    letter-spacing: 0.6px;
  }

  .person {
    position: absolute;
    left: 40px;
    top: 160px;
  }
  .person__name {
    margin: 0;
    font-size: 24px;
    font-weight: 700;
    color: var(--navy);
  }
  .person__role {
    margin: 2px 0 0;
    font-size: 19px;
    color: var(--text-grey);
  }

  .contact {
    position: absolute;
    right: 34px;
    top: 296px;
    margin: 0;
    padding: 0;
    list-style: none;
    text-align: right;
    color: var(--paper);
    font-size: 18px;
    line-height: 26px;
  }
  .contact__item {
    display: flex;
    justify-content: flex-end;
    align-items: center;
    gap: 8px;
  }
  .contact__icon {
    width: 14px;
    height: 14px;
    fill: var(--paper);
  }

  .back-mark {
    position: absolute;
    inset: 0;
    display: flex;
    align-items: center;
    justify-content: center;
    gap: 24px;
  }
  .back-mark__square {
    width: 56px;
    height: 56px;
    background: var(--grey);
  }
  .back-mark__initials {
    font-size: 150px;
    font-weight: 600;
    color: var(--navy);
    letter-spacing: 12px;
    line-height: 1;
  }
</style>
</head>
<body>
<main class="sheet">

  <section class="card card--front" aria-label="Business card front">
    <svg class="card__wave" viewBox="0 0 640 414" preserveAspectRatio="none" aria-hidden="true">
      <path d="M0,168 C150,250 380,286 640,280 L640,292 C380,300 150,272 0,196 Z" fill="var(--grey-light)"/>
      <path d="M0,200 C150,276 380,304 640,296 L640,414 L0,414 Z" fill="var(--navy)"/>
    </svg>

    <div class="brand">
      <div class="brand__mark">
        <span class="brand__square"></span>
        <span class="brand__initials">BWP</span>
      </div>
      <div class="brand__words">
        <p class="brand__name">Brindlewood<br>Partners Ltd</p>
        <div class="brand__tagline">Excellence in Medical Legal Reporting</div>
      </div>
    </div>

    <div class="person">
      <p class="person__name">Tomas Wheeler</p>
      <p class="person__role">Consultant Orthotist &amp; Expert Witness</p>
    </div>

    <ul class="contact">
      <li class="contact__item">
        <svg class="contact__icon" viewBox="0 0 24 24" aria-hidden="true"><path d="M6.6 10.8a15.2 15.2 0 0 0 6.6 6.6l2.2-2.2a1 1 0 0 1 1-.25 11.4 11.4 0 0 0 3.6.57 1 1 0 0 1 1 1V20a1 1 0 0 1-1 1A17 17 0 0 1 3 4a1 1 0 0 1 1-1h3.5a1 1 0 0 1 1 1c0 1.25.2 2.45.57 3.57a1 1 0 0 1-.25 1z"/></svg>
        +44 (0) 7700 938271
      </li>
      <li class="contact__item">
        <svg class="contact__icon" viewBox="0 0 24 24" aria-hidden="true"><path d="M2 5h20v14H2zM4 7v.5l8 5 8-5V7l-8 5z"/></svg>
        tomas@brindlewoodpartners.co.uk
      </li>
      <li class="contact__item">
        <svg class="contact__icon" viewBox="0 0 24 24" aria-hidden="true"><path d="M6 2h10v6H6zM3 9h18v10h-3v3H6v-3H3zm5 6v5h8v-5z"/></svg>
        +44 (0) 7654 8820
      </li>
      <li class="contact__item">18 Larkspur Row Kingsford, Surrey, KT9 4QP</li>
    </ul>
  </section>

  <section class="card card--back" aria-label="Business card back">
    <div class="back-mark">
      <span class="back-mark__square"></span>
      <span class="back-mark__initials">BWP</span>
    </div>
  </section>

</main>
</body>
</html>
```